BRIGHT RIVER POWER.

I'd like my business logo.
contact name: Dennis Halvorsen
phone:0438759164
email: info@brightriverpower.net.au
website: www.brightriverpower.net.au

services:
solar
battery storage
LED lighting
energy saving solutions
general electrical
I'd like the design to look professional

Target Market(s)

Everyone

Industry/Entity Type

Business

Contact Information for Business Card

as described above

Requirements
Must have
• Id like the colours and the design to work well with my logo.

```html
<!DOCTYPE html>
<html lang="en">
<head>
<meta charset="utf-8">
<title>Bright River Power – Business Card</title>
<link rel="stylesheet" href="https://fonts.googleapis.com/css2?family=Open+Sans:wght@400;600;700&display=swap">
<style>
  :root {
    --backdrop: #4d4d4d;
    --card-white: #ffffff;
    --brand-green: #4aa83a;
    --green-light: #8cc63f;
    --green-deep: #3f9f35;
    --sun-orange: #f6a01a;
    --text-grey: #555555;
    --white: #ffffff;
  }
  * { margin: 0; padding: 0; box-sizing: border-box; }
  html, body {
    width: 1105px;
    height: 1200px;
    overflow: hidden;
    background: var(--backdrop);
    font-family: "Open Sans", sans-serif;
  }
  .sheet { position: relative; width: 1105px; height: 1200px; }

  .card {
    position: absolute;
    left: 193px;
    width: 719px;
    height: 410px;
    overflow: hidden;
  }
  .card--front { top: 167px; background: var(--card-white); }
  .card--back {
    top: 622px;
    background: radial-gradient(ellipse at 50% 40%, var(--green-light) 0%, #6cb93a 45%, var(--green-deep) 100%);
    color: var(--white);
    text-align: center;
  }

  .brand {
    display: flex;
    align-items: center;
    gap: 12px;
    font-weight: 700;
    letter-spacing: 0.5px;
  }
  .brand__dot {
    width: 22px;
    height: 22px;
    border-radius: 50%;
    background: var(--sun-orange);
    flex: none;
  }
  .card--front .brand {
    position: absolute;
    left: 36px;
    top: 92px;
    font-size: 36px;
    color: var(--brand-green);
  }
  .card--back .brand {
    justify-content: center;
    margin-top: 168px;
    font-size: 44px;
    color: var(--white);
  }
  .card--back .brand__dot { background: var(--white); width: 26px; height: 26px; }

  .contact {
    position: absolute;
    left: 50px;
    top: 283px;
    list-style: none;
    font-size: 18px;
    color: var(--text-grey);
  }
  .contact__item {
    display: flex;
    align-items: center;
    gap: 9px;
    height: 27.5px;
  }
  .contact__icon { width: 16px; height: 16px; fill: var(--brand-green); flex: none; }

  .holder {
    position: absolute;
    right: 45px;
    top: 312px;
    font-size: 24px;
    font-weight: 700;
    color: var(--brand-green);
  }

  .services {
    margin-top: 62px;
    font-size: 19px;
    line-height: 28px;
  }
</style>
</head>
<body>
<main class="sheet">

  <section class="card card--front" aria-label="Business card front">
    <div class="brand"><span class="brand__dot"></span>BRIGHT RIVER POWER</div>

    <ul class="contact">
      <li class="contact__item">
        <svg class="contact__icon" viewBox="0 0 16 16" aria-hidden="true"><path d="M3.2 1.2l2.4-.4 1.4 3.4-1.6 1.2c.8 1.8 2.2 3.2 4 4l1.2-1.6 3.4 1.4-.4 2.4c-.2 1-1 1.6-2 1.6C6 13.2 2.8 10 1.6 3.2c0-1 .6-1.8 1.6-2z"/></svg>
        0438759164
      </li>
      <li class="contact__item">
        <svg class="contact__icon" viewBox="0 0 16 16" aria-hidden="true"><path d="M1 3h14v10H1z M1.8 3.8L8 8.6l6.2-4.8" fill="var(--brand-green)"/><path d="M1.6 3.8L8 8.8l6.4-5" fill="none" stroke="#fff" stroke-width="1.2"/></svg>
        info@brightriverpower.net.au
      </li>
      <li class="contact__item">
        <svg class="contact__icon" viewBox="0 0 16 16" aria-hidden="true"><circle cx="8" cy="8" r="7"/><path d="M4 5c1.5 0 2 1 3 1.5S6 9 5 9.5 3.5 11 3.5 12M10 3c0 1.5 1 2 2 2.5M9 10c1 0 2 .5 2.5 2" fill="none" stroke="#fff" stroke-width="1.3"/></svg>
        www.brightriverpower.net.au
      </li>
    </ul>

    <p class="holder">Dennis Halvorsen</p>
  </section>

  <section class="card card--back" aria-label="Business card back">
    <div class="brand"><span class="brand__dot"></span>BRIGHT RIVER POWER</div>
    <p class="services">Solar &bull; Battery storage &bull; LED lighting<br>Energy saving solutions</p>
  </section>

</main>
</body>
</html>
```